BQR, LLC Original

I need a business card design for a new company in Gaithersburg, MD. Though the name of the company is Wiremasters Of Northfield (BQR) we specialize in commercial kitchen ventilation systems as a complete turnkey project or as a service provider. We can design the entire system including the hoods, fans, ductwork, and fire system. We also specialize in fire alarm service, design, install and inspection. We are experts on any Ventaro Dynamics equipment including Pulsar VXM, Pulsar Canopies, EMS controls, Standard controls, PCU filtration and Make-up Air units with heaters and cooling. We can repair/retrofit old water wash hood systems as well. We are experts with local code requirements and upgrades.

Industry/Entity Type

Business

Contact Information for Business Card

Dale Pruitt, Wiremasters Of Northfield, LLC; 240-555-0187 Cell, Northfield, MD 20999. Dalep@wiremastersnorthfield.example

```html
<!DOCTYPE html>
<html lang="en">
<head>
<meta charset="utf-8">
<title>Wiremasters, LLC — Business Card</title>
<link href="https://fonts.googleapis.com/css2?family=Patrick+Hand&display=swap" rel="stylesheet">
<style>
  :root {
    --bg: #d9cfc4;
    --card: #161616;
    --ink: #ffffff;
    --accent: #f2e21b;
  }
  html, body {
    margin: 0;
    padding: 0;
    width: 1200px;
    height: 848px;
    overflow: hidden;
    background: var(--bg);
  }
  .canvas {
    width: 1200px;
    height: 848px;
    display: flex;
    align-items: center;
    justify-content: center;
    gap: 40px;
    font-family: "Patrick Hand", "Comic Sans MS", cursive;
  }
  .card {
    position: relative;
    width: 540px;
    height: 309px;
    background: var(--card);
    color: var(--ink);
    box-shadow: 0 6px 18px rgba(0,0,0,.25);
    overflow: hidden;
  }
  .rule {
    position: absolute;
    height: 2px;
    background: var(--accent);
  }
  .rule--upper { left: 372px; right: 0; top: 128px; }
  .rule--middle { left: 0; width: 168px; top: 172px; }
  .rule--bottom { left: 0; right: 0; top: 284px; }

  .brand {
    position: absolute;
    left: 0; right: 0;
    text-align: center;
    font-size: 36px;
    line-height: 1;
    color: var(--ink);
    letter-spacing: .5px;
    white-space: nowrap;
  }
  .brand-mark {
    display: inline-block;
    width: 16px;
    height: 16px;
    border-radius: 50%;
    background: var(--accent);
    margin-right: 10px;
    vertical-align: middle;
  }
  .front .brand { top: 70px; }
  .person {
    position: absolute;
    left: 0; right: 0;
    top: 140px;
    text-align: center;
  }
  .person-name {
    color: var(--accent);
    font-size: 30px;
    line-height: 1;
  }
  .person-role {
    font-size: 16px;
    line-height: 1.2;
  }
  .contact {
    position: absolute;
    left: 0; right: 0;
    top: 202px;
    text-align: center;
    font-size: 16px;
    line-height: 22px;
  }
  .back .brand {
    top: 50%;
    transform: translateY(-50%);
    font-size: 44px;
  }
</style>
</head>
<body>
  <main class="canvas">
    <section class="card front" aria-label="Business card front">
      <div class="brand">Wiremasters, LLC</div>
      <span class="rule rule--upper"></span>
      <div class="person">
        <div class="person-name">Dale Pruitt</div>
        <div class="person-role">Electricians</div>
      </div>
      <span class="rule rule--middle"></span>
      <div class="contact">
        <div>240-555-0187</div>
        <div>Dalep@wiremastersnorthfield.example</div>
        <div>Northfield, MD 20999</div>
      </div>
      <span class="rule rule--bottom"></span>
    </section>

    <section class="card back" aria-label="Business card back">
      <div class="brand"><span class="brand-mark"></span>Wiremasters, LLC</div>
    </section>
  </main>
</body>
</html>
```